"Career in Gradvel" | Poster design

We need a "We are hiring" poster design. We are a construction company based in Croatia and we are looking for 3 categories of construction workers. We want moder, serious and powerful poster . In attachment you can find our logo. The font of a text that is used in logo design is "nexa bold".

At the bottom (or where designer can see it) will be description of general condition. The poster must be simple and clear.

Target Market(s)

Wide range of employment

Industry/Entity Type

Construction Company

Colors

Designer to choose colors to be used in the design.

Requirements
Must have
• The text in poster that will be needed is "Mason/carpenter job", "Steel-bender job" and "Auxiliary worker". This terms may be wrong, but it will be translated in local language. Under all of them will be a short descrtiption row, and one row of salary. This is for all three categories.
• At the bottom (or where designer can see it) will be description of general condition. The poster must be simple and clear.

```html
<!DOCTYPE html>
<html lang="en">
<head>
<meta charset="utf-8">
<title>Gradvel – We Are Hiring</title>
<link href="https://fonts.googleapis.com/css2?family=Montserrat:wght@500;600;700;800&family=Raleway:wght@200&display=swap" rel="stylesheet">
<style>
  :root {
    --orange: #e8913f;
    --ink: #161616;
    --grey-text: #5f5f5f;
    --grey-mark: #6e6e6e;
    --bg-light: #eeeeee;
    --bg-mid: #dcdcdc;
  }
  * { margin: 0; padding: 0; box-sizing: border-box; }
  html, body { width: 1000px; height: 1200px; overflow: hidden; }
  body { background: var(--bg-light); font-family: "Montserrat", sans-serif; color: var(--ink); }
  .poster {
    position: relative;
    width: 1000px;
    height: 1200px;
    overflow: hidden;
  }
  .poster-texture {
    position: absolute;
    inset: 0;
    background: linear-gradient(135deg, var(--bg-mid) 0%, #f2f2f2 35%, var(--bg-mid) 60%, #efefef 85%, var(--bg-mid) 100%);
  }
  .poster-content > * {
    position: absolute;
    left: 0;
    right: 0;
    text-align: center;
    line-height: 1;
  }
  .brand-square {
    left: 420px;
    right: auto;
    top: 70px;
    width: 160px;
    height: 160px;
    border: 5px solid var(--grey-mark);
  }
  .brand-name {
    top: 262px;
    font-weight: 500;
    font-size: 92px;
    letter-spacing: 4px;
    color: var(--orange);
  }
  .brand-tagline {
    top: 378px;
    font-weight: 600;
    font-size: 19px;
    letter-spacing: 0.5px;
    color: var(--grey-text);
  }
  .headline-intro {
    top: 455px;
    font-family: "Raleway", sans-serif;
    font-weight: 200;
    font-size: 104px;
    color: var(--ink);
  }
  .headline-main {
    top: 560px;
    font-weight: 800;
    font-size: 180px;
    letter-spacing: -2px;
    color: var(--orange);
  }
  .job-list {
    top: 752px;
    list-style: none;
  }
  .job-list li {
    font-weight: 600;
    font-size: 52px;
    line-height: 78px;
    color: var(--ink);
  }
  .details-bar {
    left: 155px;
    right: 155px;
    top: 1000px;
    height: 60px;
    background: var(--orange);
    display: flex;
    align-items: center;
    justify-content: center;
    font-weight: 600;
    font-size: 19px;
    color: var(--ink);
  }
  .call-line {
    top: 1100px;
    font-weight: 700;
    font-size: 46px;
    color: var(--ink);
  }
  .call-line .phone { color: var(--orange); }
</style>
</head>
<body>
  <main class="poster">
    <div class="poster-texture" role="img" aria-label="Light grey low-poly geometric background texture"></div>
    <div class="poster-content">
      <div class="brand-square" aria-hidden="true"></div>
      <h1 class="brand-name">GRADVEL</h1>
      <p class="brand-tagline">IZVOĐENJE I VOĐENJE GRAĐEVINSKIH RADOVA</p>
      <p class="headline-intro">WE ARE</p>
      <p class="headline-main">HIRING</p>
      <ul class="job-list">
        <li>Mason/carpenter</li>
        <li>Steel-bender</li>
        <li>Auxiliary worker</li>
      </ul>
      <p class="details-bar">short descrtiption row, and one row of salary</p>
      <p class="call-line">CALL NOW - <span class="phone">0987 654 321</span></p>
    </div>
  </main>
</body>
</html>
```